Modern Business Card

Modern professional business card with more than just logo and demographic info. Something memorable.

We are a trendy/modern chiropractic group with an emphasis on neurology, hence the minimalist-type brain logo. We want to convey that modern and technical aspect with professionalism and the elite nature of our practice environment.

```html
<!DOCTYPE html>
<html lang="en">
<head>
<meta charset="UTF-8">
<title>Vantage Chiropractic — Business Card</title>
<link href="https://fonts.googleapis.com/css2?family=Cinzel:wght@400;500&family=Poppins:wght@400&display=swap" rel="stylesheet">
<style>
  :root {
    --page-bg: #e6e7e9;
    --card-dark: #1b1b1c;
    --card-light: #ffffff;
    --brand-blue: #3f76ba;
    --ink: #1c1c1c;
    --muted: #4a4a4a;
    --white: #ffffff;
  }
  * { margin: 0; padding: 0; box-sizing: border-box; }
  html, body {
    width: 1200px; height: 960px; overflow: hidden;
    background: var(--page-bg);
  }
  .sheet {
    width: 1200px; height: 960px;
    display: flex; flex-direction: column; align-items: center; justify-content: center;
    gap: 48px;
  }
  .card {
    position: relative;
    width: 700px; height: 400px;
    border-radius: 24px;
    overflow: hidden;
    box-shadow: 0 10px 28px rgba(0,0,0,0.18);
  }

  /* Back side */
  .card--back {
    background: var(--card-dark);
    display: flex; align-items: center; justify-content: center;
  }
  .wordmark {
    display: flex; align-items: center; gap: 20px;
    font-family: "Cinzel", serif; color: var(--white);
  }
  .wordmark__square {
    width: 58px; height: 58px; background: var(--brand-blue);
    border-radius: 6px;
  }
  .wordmark__text { display: flex; flex-direction: column; line-height: 1; }
  .wordmark__name { font-size: 52px; font-weight: 400; letter-spacing: 2px; }
  .wordmark__sub { font-size: 52px; font-weight: 400; letter-spacing: 2px; margin-top: 2px; }

  /* Front side */
  .card--front { background: var(--card-light); }
  .front__band {
    position: absolute; top: 0; right: 0;
    width: 300px; height: 100%;
  }
  .identity {
    position: absolute; left: 48px; top: 118px;
    font-family: "Cinzel", serif;
  }
  .identity__name { color: var(--brand-blue); font-size: 26px; font-weight: 500; letter-spacing: 1px; }
  .identity__title { color: var(--ink); font-size: 15px; letter-spacing: 1.5px; margin-top: 2px; }
  .contact {
    position: absolute; left: 48px; top: 214px;
    font-family: "Poppins", sans-serif; font-size: 15px; line-height: 21px;
    color: var(--muted);
  }
  .contact__address { margin-bottom: 12px; }
  .contact__label { color: var(--brand-blue); }
  .contact__web { color: var(--brand-blue); }
</style>
</head>
<body>
  <main class="sheet">
    <section class="card card--back" aria-label="Card back">
      <div class="wordmark">
        <span class="wordmark__square" aria-hidden="true"></span>
        <div class="wordmark__text">
          <span class="wordmark__name">Vantage</span>
          <span class="wordmark__sub">Chiropractic</span>
        </div>
      </div>
    </section>

    <section class="card card--front" aria-label="Card front">
      <svg class="front__band" viewBox="0 0 300 400" aria-hidden="true">
        <path d="M120 0 H300 V400 H60 Q40 400 40 380 V150 Q40 120 70 120 H120 Z" fill="var(--brand-blue)"/>
      </svg>
      <div class="identity">
        <div class="identity__name">Daniel Reyes</div>
        <div class="identity__title">President</div>
      </div>
      <div class="contact">
        <div class="contact__address">4120 Birchwood Court<br>Juneau, Alaska 34512</div>
        <div><span class="contact__label">P:</span> 555-214-7730</div>
        <div><span class="contact__label">C:</span> 555-618-2049</div>
        <div><span class="contact__label">F:</span> 555-377-9162</div>
        <div>info@vantagechiro.com</div>
        <div class="contact__web">www.vantagechiro.com</div>
      </div>
    </section>
  </main>
</body>
</html>
```